Stonebrace Business Card Design

The Stonebrace Co is an aggregate (crushing) equipment dealer serving Western Canadian provinces. Stonebrace is a distributor of aggregate equipment for different manufacturers.

We are looking to change and update the existing business card which has been used since the existence of the company. A copy of existing card has been attached for reference. The Stonebrace Co logo we want to remain the same and we want the green color to remain the same.

We are wanting something new with a different look. A refreshing card to show a new modern and updated look. No longer wanting to have the manufacturers on the back of the card but something more like our logo on the back of the card with a statement like "Crushing Solutions"

ideas could be:
- card can be different colors on front and back
- front or reverse of the card could possibly be the green color with the logo in black

Target Market(s)

Owners of Aggregate/Crushing companies

Contact Information for Business Card

see above

Requirements
Must have
• - logo to remain same along with same font within logo
• - green color to remain same
Nice to have
• as noted above under project description
Should not have

```html
<!DOCTYPE html>
<html lang="en">
<head>
<meta charset="utf-8">
<title>Stonebrace Business Card</title>
<link rel="stylesheet" href="https://fonts.googleapis.com/css2?family=Roboto:wght@400;500;700&family=Roboto+Condensed:wght@700&display=swap">
<style>
  :root {
    --brand-green: #878a0b;
    --ink: #231f20;
    --text-grey: #444444;
    --card-white: #f3f3f3;
    --page-bg: #e6e3df;
  }
  * { margin: 0; padding: 0; box-sizing: border-box; }
  html, body { width: 1200px; height: 960px; overflow: hidden; }
  body {
    background: var(--page-bg);
    font-family: "Roboto", Arial, sans-serif;
    position: relative;
  }
  .card {
    position: absolute;
    left: 320px;
    width: 600px;
    height: 342px;
    border-radius: 22px;
    overflow: hidden;
  }
  .card-back {
    top: 108px;
    background: var(--brand-green);
  }
  .card-back .brand-lockup {
    position: absolute;
    top: 150px;
    left: 0;
    width: 600px;
    display: flex;
    justify-content: center;
    align-items: center;
    gap: 22px;
  }
  .brand-dot {
    width: 46px;
    height: 46px;
    border-radius: 50%;
    background: var(--ink);
  }
  .card-back .brand-name {
    font-weight: 700;
    font-size: 22px;
    color: var(--ink);
    letter-spacing: 0.2px;
  }
  .tagline {
    position: absolute;
    top: 292px;
    width: 600px;
    text-align: center;
    font-weight: 500;
    font-size: 14px;
    color: var(--ink);
  }
  .card-front {
    top: 493px;
    background: var(--brand-green);
  }
  .header-swoosh {
    position: absolute;
    top: 0;
    left: 0;
  }
  .person {
    position: absolute;
    top: 24px;
    right: 32px;
    text-align: right;
    color: #ffffff;
  }
  .person-name {
    font-family: "Roboto Condensed", Arial, sans-serif;
    font-weight: 700;
    font-size: 21px;
    line-height: 26px;
  }
  .person-title {
    font-size: 14px;
    line-height: 20px;
  }
  .card-front .brand-dot {
    position: absolute;
    top: 116px;
    left: 46px;
    width: 50px;
    height: 50px;
    background: var(--brand-green);
  }
  .card-front .brand-name {
    position: absolute;
    top: 199px;
    left: 32px;
    font-weight: 700;
    font-size: 16px;
    color: var(--ink);
  }
  .contact-list {
    position: absolute;
    top: 244px;
    left: 28px;
    list-style: none;
  }
  .contact-list li {
    display: flex;
    align-items: center;
    gap: 8px;
    font-size: 14px;
    line-height: 19.5px;
    color: var(--text-grey);
  }
  .contact-list svg { width: 14px; height: 14px; fill: var(--brand-green); }
  .address {
    position: absolute;
    top: 265px;
    right: 32px;
    text-align: right;
    font-size: 14px;
    line-height: 19.5px;
    color: var(--text-grey);
    font-style: normal;
  }
</style>
</head>
<body>

<section class="card card-back">
  <div class="brand-lockup">
    <span class="brand-dot"></span>
    <span class="brand-name">THE STONEBRACE CO.</span>
  </div>
  <p class="tagline">Crushing Solutions</p>
</section>

<section class="card card-front">
  <svg class="header-swoosh" width="600" height="342" viewBox="0 0 600 342">
    <path class="white-field" d="M0,116 C50,38 140,16 230,36 C330,60 450,112 600,100 L600,342 L0,342 Z" fill="var(--card-white)"/>
    <path class="ink-swoosh" d="M36,64 C100,24 170,16 236,30 C340,56 460,110 600,92 L600,106 C460,122 340,70 236,40 C170,26 100,34 36,64 Z" fill="var(--ink)"/>
    <path class="green-swoosh" d="M0,122 C40,58 150,30 265,66 C150,44 60,64 0,130 Z" fill="var(--brand-green)"/>
  </svg>

  <div class="person">
    <div class="person-name">DALE MORROW</div>
    <div class="person-title">CEO/FOUNDER</div>
  </div>

  <span class="brand-dot"></span>
  <span class="brand-name">THE STONEBRACE CO.</span>

  <ul class="contact-list">
    <li><svg viewBox="0 0 14 14"><path d="M3 1 L5 1 L6 4 L4.5 5.5 C5.3 7.3 6.7 8.7 8.5 9.5 L10 8 L13 9 L13 11 C13 12 12 13 11 13 C6 13 1 8 1 3 C1 2 2 1 3 1 Z"/></svg>780.555.0142</li>
    <li><svg viewBox="0 0 14 14"><path d="M4 0 H10 A1 1 0 0 1 11 1 V13 A1 1 0 0 1 10 14 H4 A1 1 0 0 1 3 13 V1 A1 1 0 0 1 4 0 Z M4.5 2 V11 H9.5 V2 Z"/></svg>780.555.0187</li>
    <li><svg viewBox="0 0 14 14"><path d="M4 1 H10 V5 H4 Z M1 6 H13 V11 H11 V13 H3 V11 H1 Z M4 9 V12 H10 V9 Z"/></svg>780.555.0163</li>
    <li><svg viewBox="0 0 14 14"><path d="M1 3 H13 V11 H1 Z M1.5 3.5 L7 8 L12.5 3.5" /></svg>dale@stonebr.com</li>
  </ul>

  <address class="address">
    2218- 48B Avenue<br>
    Nisku, Alberta T9E 3K1<br>
    www.stonebrace.ca
  </address>
</section>

</body>
</html>
```